holloway paving service

Needs to have phone number 0418259730 and email markholloway@brightmail.com.au.
ABN 62318470915
name mark holloway

For all your concreting solutions
Excavation
Exposed & colour concrete
House & shed slabs
Driveways
Landing & steps

Contact Information for Business Card

ph 0418259730
email markholloway@brightmail.com.au.
ABN 62318470915
name mark holloway

```html
<!DOCTYPE html>
<html lang="en">
<head>
<meta charset="utf-8">
<title>Holloway Paving Service – Business Card</title>
<link href="https://fonts.googleapis.com/css2?family=Montserrat:wght@400;500;600;700&display=swap" rel="stylesheet">
<style>
  :root {
    --orange: #ee6a22;
    --orange-light: #f3813a;
    --orange-deep: #e85d1c;
    --grey: #6d6e70;
    --ink: #4a4a4a;
    --paper: #f7f7f7;
    --stage: #e4e2df;
    --white: #ffffff;
  }
  * { box-sizing: border-box; margin: 0; padding: 0; }
  html, body { width: 1200px; height: 886px; overflow: hidden; }
  body {
    background: var(--stage);
    font-family: "Montserrat", Arial, sans-serif;
    position: relative;
  }
  .card {
    position: absolute;
    left: 320px;
    width: 560px;
    height: 342px;
    overflow: hidden;
    box-shadow: 0 6px 18px rgba(0,0,0,0.18);
  }

  /* Front */
  .card-front { top: 70px; background: var(--paper); }
  .name-band {
    position: absolute;
    left: 0; top: 58px;
    width: 290px; height: 56px;
    background: var(--orange);
    display: flex; align-items: center;
    padding-left: 48px;
  }
  .name-band .person {
    color: var(--white);
    font-weight: 700;
    font-size: 19px;
    letter-spacing: 0.3px;
    text-transform: uppercase;
  }
  .brand-mark {
    position: absolute;
    left: 276px; top: 62px;
    width: 46px; height: 46px;
    background: var(--grey);
    border: 3px solid var(--white);
    transform: rotate(45deg);
    outline: 2px solid var(--grey);
  }
  .divider {
    position: absolute;
    left: 350px; top: 44px;
    width: 1.5px; height: 82px;
    background: var(--orange);
  }
  .brand-block {
    position: absolute;
    left: 364px; top: 44px;
  }
  .brand-block .company {
    color: var(--orange);
    font-weight: 600;
    font-size: 15px;
    text-transform: uppercase;
    letter-spacing: 0.2px;
  }
  .brand-block .sub {
    display: flex; align-items: center; gap: 8px;
    margin-top: 4px;
  }
  .brand-block .sub .rule { width: 40px; height: 1.5px; background: var(--grey); }
  .brand-block .sub span {
    color: var(--grey);
    font-size: 11px;
    letter-spacing: 2px;
    text-transform: uppercase;
  }
  .brand-block .tel {
    color: var(--orange);
    font-size: 12px;
    letter-spacing: 1.5px;
    margin-top: 4px;
  }
  .contact-list {
    position: absolute;
    left: 54px; top: 218px;
    list-style: none;
    color: var(--ink);
    font-size: 13px;
    line-height: 24px;
  }
  .contact-list li { display: flex; align-items: center; gap: 9px; }
  .contact-list svg { width: 11px; height: 11px; flex: none; }
  .contact-list .abn { padding-left: 20px; }

  /* Back */
  .card-back {
    top: 474px;
    background: linear-gradient(135deg, var(--orange-light), var(--orange-deep));
    color: var(--white);
  }
  .faint-square {
    position: absolute;
    left: 150px; top: -70px;
    width: 190px; height: 190px;
    background: rgba(255,255,255,0.13);
    transform: rotate(45deg);
  }
  .faint-name {
    position: absolute;
    left: 0; right: 0; top: 58px;
    text-align: center;
    font-weight: 700;
    font-size: 18px;
    color: rgba(255,255,255,0.22);
    text-transform: uppercase;
    letter-spacing: 1px;
  }
  .back-brand {
    position: absolute;
    left: 34px; top: 196px;
  }
  .back-brand .company {
    font-weight: 700;
    font-size: 17px;
    text-transform: uppercase;
  }
  .back-brand .sub {
    display: flex; align-items: center; gap: 8px; margin-top: 4px;
  }
  .back-brand .sub .rule { width: 44px; height: 1.5px; background: var(--white); }
  .back-brand .sub span { font-size: 12px; letter-spacing: 2px; text-transform: uppercase; }
  .back-brand .tel { font-size: 13px; letter-spacing: 2px; margin-top: 4px; }
  .back-brand .web { font-size: 11px; letter-spacing: 3px; margin-top: 6px; }
  .services {
    position: absolute;
    right: 30px; top: 150px;
    list-style: none;
    text-align: right;
    font-size: 13px;
    line-height: 23px;
  }
  .services li::after {
    content: "";
    display: inline-block;
    width: 5px; height: 5px;
    background: var(--white);
    margin-left: 8px;
    vertical-align: middle;
  }
</style>
</head>
<body>

<section class="card card-front" aria-label="Business card front">
  <div class="name-band"><span class="person">Mark Holloway</span></div>
  <div class="brand-mark" aria-hidden="true"></div>
  <div class="divider"></div>
  <div class="brand-block">
    <p class="company">Holloway Paving Service</p>
    <div class="sub"><div class="rule"></div><span>Solutions</span></div>
    <p class="tel">0418259730</p>
  </div>
  <ul class="contact-list">
    <li>
      <svg viewBox="0 0 12 12" aria-hidden="true"><path fill="#ee6a22" d="M2.5 1l2 .2.8 2.4-1.3 1c.7 1.4 1.6 2.3 3 3l1-1.3 2.4.8.1 2c-.2.6-.8 1-1.5 1C4.8 10.2 1.8 7.2 1.7 3c0-.8.3-1.7.8-2z"/></svg>
      0418259730
    </li>
    <li>
      <svg viewBox="0 0 12 12" aria-hidden="true"><rect x="0.5" y="2" width="11" height="8" fill="#ee6a22"/><path d="M1 2.5l5 4 5-4" stroke="#fff" stroke-width="1" fill="none"/></svg>
      markholloway@brightmail.com.au
    </li>
    <li>
      <svg viewBox="0 0 12 12" aria-hidden="true"><circle cx="6" cy="6" r="5.5" fill="#ee6a22"/><path d="M.8 6h10.4M6 .5c-2.5 3-2.5 8 0 11M6 .5c2.5 3 2.5 8 0 11" stroke="#fff" stroke-width=".8" fill="none"/></svg>
      www.hollowaypaving.com.au
    </li>
    <li class="abn">ABN 62318470915</li>
  </ul>
</section>

<section class="card card-back" aria-label="Business card back">
  <div class="faint-square" aria-hidden="true"></div>
  <p class="faint-name" aria-hidden="true">Holloway Paving Service</p>
  <div class="back-brand">
    <p class="company">Holloway Paving Service</p>
    <div class="sub"><div class="rule"></div><span>Solutions</span></div>
    <p class="tel">0418259730</p>
    <p class="web">www.hollowaypaving.com.au</p>
  </div>
  <ul class="services">
    <li>Excavation</li>
    <li>Exposed &amp; colour concrete</li>
    <li>House &amp; shed slabs</li>
    <li>Driveways</li>
    <li>Landing &amp; steps</li>
  </ul>
</section>

</body>
</html>
```